Business Card for Polygraph business in Africa

Business Card . Polygraph Examiner based in Tanzania, East Africa.
Business Card will be used to disseminate contact information to potential clients.
It should convey that I am a professional specifically in the polygraph field and perform my work with integrity.

I have attached the business card that I'm currently using, which I threw together myself initially. It's not professional enough.

Target Market(s)

Banks, Accounting Firms, Government Ministries, Gas, Oil, & Gemstone Mining Concerns, Wildlife Conservation NGOs, International companies located in East Africa.

Industry/Entity Type

Business

Contact Information for Business Card

Veritrace Kilonga
Miriam Holloway
PO Box 48317
Arusha, Tanzania
+255 612 839 274
miriamholloway@postvale.example

Colors
00a990
f37122
faa54b

Requirements
Must have
• - Veritrace Kilonga (with the word "Polygraph" being more prominent than the word "Tanzania")
• - Forensic Examinations
• - Employment Screening
• - Should contain a logo of the Continental Truthline Society (of which I'm a member)
• - I would like an accent design (such as the polygraph "squiggles" of a cardio tracing or such as that)
• - My contact information (less prominent, but large enough to read legibly). I would also consider putting the contact information on the second side of the card.
Nice to have
• My color suggestions are changeable.
Should not have
• Anything "cutesy" or "cartoonish"

```html
<!DOCTYPE html>
<html lang="en">
<head>
<meta charset="utf-8">
<title>Veritrace Kilonga – Business Card</title>
<link rel="stylesheet" href="https://fonts.googleapis.com/css2?family=Roboto:wght@400;500;700&family=Roboto+Condensed:wght@700&display=swap">
<style>
  :root {
    --backdrop: #2a2a2a;
    --card-front: #f2f2f2;
    --card-back: #0e1a45;
    --navy: #0e1a45;
    --ring: #333d3f;
    --ink: #3a3a3a;
    --ink-soft: #555555;
    --white: #ffffff;
  }
  * { margin: 0; padding: 0; box-sizing: border-box; }
  html, body {
    width: 1200px; height: 960px; overflow: hidden;
    background: var(--backdrop);
    font-family: "Roboto", Arial, sans-serif;
  }
  .stage { position: relative; width: 1200px; height: 960px; }

  .card {
    position: absolute;
    width: 600px; height: 343px;
    border-radius: 18px;
  }
  .card--front { left: 314px; top: 113px; background: var(--card-front); }
  .card--back  { left: 311px; top: 473px; background: var(--card-back); }

  /* Front: contact column */
  .member-badge {
    position: absolute; left: 36px; top: 94px;
    width: 68px; height: 68px; border-radius: 50%;
    border: 3px solid var(--navy);
    background: var(--white);
  }
  .holder-name {
    position: absolute; left: 36px; top: 174px;
    font-family: "Roboto Condensed", "Arial Narrow", sans-serif;
    font-weight: 700; font-size: 21px; line-height: 26px; color: var(--navy);
  }
  .holder-company {
    position: absolute; left: 36px; top: 201px;
    font-weight: 500; font-size: 15px; line-height: 20px; color: var(--ink);
  }
  .holder-address {
    position: absolute; left: 36px; top: 232px;
    font-size: 14px; line-height: 18px; color: var(--ink-soft);
  }
  .contact-list {
    position: absolute; left: 36px; top: 276px;
    list-style: none; font-size: 14px; color: var(--ink-soft);
  }
  .contact-list li { display: flex; align-items: center; height: 20px; }
  .contact-list svg { width: 12px; height: 12px; margin-right: 9px; fill: var(--navy); }

  /* Front: brand block */
  .front-brand {
    position: absolute; left: 258px; top: 0; width: 330px; height: 343px;
    display: flex; align-items: center; gap: 22px;
  }
  .front-brand__circle {
    flex: none; width: 120px; height: 120px; border-radius: 50%;
    border: 11px solid var(--ring);
  }
  .front-brand__name {
    font-weight: 700; font-size: 40px; line-height: 46px; color: var(--navy);
  }

  /* Back */
  .back-brand {
    position: absolute; left: 0; top: 120px; width: 600px; height: 100px;
    display: flex; align-items: center; justify-content: center; gap: 14px;
  }
  .back-brand__circle {
    flex: none; width: 86px; height: 86px; border-radius: 50%;
    border: 6px solid var(--white);
  }
  .back-brand__name {
    font-weight: 700; font-size: 38px; color: var(--white);
  }
  .services {
    position: absolute; left: 0; top: 287px; width: 600px;
    text-align: center;
    font-size: 14.5px; color: var(--white);
  }
  .services .dot {
    display: inline-block; width: 6px; height: 6px; border-radius: 50%;
    background: var(--white); margin: 0 8px; vertical-align: middle;
  }
</style>
</head>
<body>
<main class="stage">
  <section class="card card--front">
    <div class="member-badge" role="img" aria-label="Continental Truthline Society membership badge"></div>
    <h1 class="holder-name">Miriam Holloway</h1>
    <p class="holder-company">Veritrace Kilonga</p>
    <p class="holder-address">PO Box 48317<br>Arusha, Tanzania</p>
    <ul class="contact-list">
      <li>
        <svg viewBox="0 0 24 24" aria-hidden="true"><path d="M6.6 10.8a15.1 15.1 0 0 0 6.6 6.6l2.2-2.2c.3-.3.7-.4 1-.2 1.1.4 2.3.6 3.6.6.6 0 1 .4 1 1V20c0 .6-.4 1-1 1A17 17 0 0 1 3 4c0-.6.4-1 1-1h3.5c.6 0 1 .4 1 1 0 1.3.2 2.5.6 3.6.1.3 0 .7-.2 1z"/></svg>
        +255 612 839 274
      </li>
      <li>
        <svg viewBox="0 0 24 24" aria-hidden="true"><path d="M2 5h20v2l-10 7L2 7z"/><path d="M2 9l10 7 10-7v10H2z"/></svg>
        miriamholloway@postvale.example
      </li>
    </ul>
    <div class="front-brand">
      <span class="front-brand__circle" aria-hidden="true"></span>
      <p class="front-brand__name">Veritrace<br>Kilonga</p>
    </div>
  </section>

  <section class="card card--back">
    <div class="back-brand">
      <span class="back-brand__circle" aria-hidden="true"></span>
      <p class="back-brand__name">Veritrace Kilonga</p>
    </div>
    <p class="services">Forensic Examinations<span class="dot"></span>Employment Screening</p>
  </section>
</main>
</body>
</html>
```